Professional violinist needs business cards

I am trying to attract the following jobs:
-private violin lessons (primarily classical)
-performance gigs (weddings, birthday parties, funerals, etc.)
-collaborations with other artists (studio recordings, performances)

I want to communicate that I have a very high standard of excellence for my work, but I also love people and celebrations.
Values/style words I like are:
love, joy, peace, fun, beauty, authenticity, excellence, warmth, refined/sleek, free spirited. If that's too confusing, just ignore :)

I will attach my favorite business card template that I could find on Canva. The lines are supposed to be like a music staff, which I think is really cool, but I also don't want it to look too busy. I like the simple black and white--I think it looks sharp--but I also am open to other ideas. I also have seen business cards with pictures included that looked great, so I attached an image that could be used as well.

I am also attaching a file that I made of my initials that could be used as a logo, but I'm not sure if it should be included.

Information on the card:
-My name (18 letters total)
-"violinist"
-phone number, email, website

Thank you!

```html
<!DOCTYPE html>
<html lang="en">
<head>
<meta charset="utf-8">
<title>Marina Ellsworthe – Violinist Business Card</title>
<link rel="stylesheet" href="https://fonts.googleapis.com/css2?family=Barlow+Condensed:wght@300;400;600&family=Barlow:wght@500;600&display=swap">
<style>
  :root {
    --backdrop: #4a4b4e;
    --card: #ffffff;
    --ink: #111111;
    --photo-dark: #2a2a2a;
    --photo-mid: #7b7b7b;
    --photo-light: #c9c9c9;
  }
  * { box-sizing: border-box; margin: 0; padding: 0; }
  html, body {
    width: 1200px; height: 1200px; overflow: hidden;
    background: var(--backdrop);
  }
  .stage { position: relative; width: 1200px; height: 1200px; }

  .card {
    position: absolute; left: 150px; width: 900px; height: 514px;
    background: var(--card); overflow: hidden;
    box-shadow: 0 12px 30px rgba(0,0,0,.35);
  }
  .card--front { top: 60px; }
  .card--back { top: 626px; }

  .photo { position: absolute; top: 0; bottom: 0; }
  .card--front .photo {
    left: 0; width: 470px;
    background: linear-gradient(90deg, var(--photo-dark) 0%, var(--photo-mid) 55%, var(--photo-light) 80%, var(--card) 100%);
  }
  .card--back .photo {
    right: 0; width: 430px;
    background: linear-gradient(270deg, var(--photo-dark) 0%, var(--photo-mid) 55%, var(--photo-light) 80%, var(--card) 100%);
  }

  .fhole-mark { display: block; }

  .name {
    font-family: "Barlow Condensed", sans-serif;
    font-size: 52px; line-height: 1; color: var(--ink);
    text-transform: uppercase; white-space: nowrap;
  }
  .name__first { font-weight: 600; }
  .name__last { font-weight: 300; }
  .role {
    font-family: "Barlow Condensed", sans-serif;
    font-weight: 400; font-size: 26px; letter-spacing: 9px;
    color: var(--ink); text-transform: uppercase;
  }

  .card--front .brand {
    position: absolute; left: 470px; top: 70px; width: 400px;
    text-align: center;
  }
  .card--front .fhole-mark { margin: 0 auto 22px; }
  .card--front .name { font-size: 46px; }

  .card--back .brand {
    position: absolute; left: 50px; top: 70px;
    display: flex; align-items: center; gap: 18px;
  }
  .card--back .name { font-size: 40px; }
  .card--back .role { font-size: 22px; letter-spacing: 8px; text-align: center; }

  .contacts {
    position: absolute; left: 80px; top: 250px; list-style: none;
    font-family: "Barlow", sans-serif; font-weight: 600;
    font-size: 30px; color: var(--ink);
  }
  .contacts li { display: flex; align-items: center; gap: 22px; margin-bottom: 26px; }
  .contacts svg { width: 34px; height: 34px; flex: none; fill: var(--ink); }
</style>
</head>
<body>
<main class="stage">

  <section class="card card--front">
    <div class="photo" role="img" aria-label="Black and white portrait photo of the violinist holding her violin against a stone wall, with a brushed edge"></div>
    <div class="brand">
      <svg class="fhole-mark" width="120" height="70" viewBox="0 0 120 70" role="img" aria-label="Violin f-hole ornament">
        <rect x="22" y="6" width="10" height="58" rx="5" fill="#111"/>
        <rect x="80" y="6" width="10" height="58" rx="5" fill="#111"/>
      </svg>
      <div class="name"><span class="name__first">Marina</span> <span class="name__last">Ellsworthe</span></div>
      <div class="role">Violinist</div>
    </div>
  </section>

  <section class="card card--back">
    <div class="photo" role="img" aria-label="Black and white portrait photo of the violinist against a stone wall, with a brushed edge"></div>
    <div class="brand">
      <svg class="fhole-mark" width="70" height="44" viewBox="0 0 70 44" role="img" aria-label="Violin f-hole ornament">
        <rect x="12" y="4" width="7" height="36" rx="3.5" fill="#111"/>
        <rect x="48" y="4" width="7" height="36" rx="3.5" fill="#111"/>
      </svg>
      <div>
        <div class="name"><span class="name__first">Marina</span> <span class="name__last">Ellsworthe</span></div>
        <div class="role">Violinist</div>
      </div>
    </div>
    <ul class="contacts">
      <li>
        <svg viewBox="0 0 24 24" aria-hidden="true"><path d="M6.6 10.8a15.1 15.1 0 0 0 6.6 6.6l2.2-2.2c.3-.3.7-.4 1-.2 1.1.4 2.3.6 3.6.6.6 0 1 .4 1 1V20c0 .6-.4 1-1 1A17 17 0 0 1 3 4c0-.6.4-1 1-1h3.5c.6 0 1 .4 1 1 0 1.3.2 2.5.6 3.6.1.3 0 .7-.2 1z"/></svg>
        <span>+00 1234 567 321</span>
      </li>
      <li>
        <svg viewBox="0 0 24 24" aria-hidden="true"><path d="M2 5h20v14H2z" fill="none" stroke="#111" stroke-width="2"/><path d="M2 5l10 8 10-8" fill="none" stroke="#111" stroke-width="2"/></svg>
        <span>marinaellsworthe@postbox.com</span>
      </li>
      <li>
        <svg viewBox="0 0 24 24" aria-hidden="true"><path d="M12 3l10 9h-3v9h-5v-6h-4v6H5v-9H2z"/></svg>
        <span>www.marinaellsworthe.com</span>
      </li>
    </ul>
  </section>

</main>
</body>
</html>
```